KVOR Individual and Corporate Development Business Card Design

KVOR needs a business card design that is aligned with it's values and targetted markets. Coherent Lattice of Adaptive Reasoning Method's self diagnosis model and tools, which can be used for personal improvement and team/business performance enhancement, is based on the learnings of over 20 years of medical practitioning. KVOR supercharges personal effectiveness and awareness to also increase team and business performance.

The targetted markets are high performance individuals and teams who aspire seek to enhance their capabilities and achieve their absolute best potential.

Look and feel for the business card design we are looking for is high technology, premium, fresh, new and medical.

Target Market(s)

Industry/Entity Type

Business Consultant

Contact Information for Business Card

Logo, Full Name, Title, Phone number, Email, company name, Address,

Font styles to use
Sans Serif

Requirements
Must have
• Tag line: Amplifying Results for Truly Driven Professionals
• Please use same colours as the logo.

```html
<!DOCTYPE html>
<html lang="en">
<head>
<meta charset="utf-8">
<title>KVOR Business Card</title>
<link href="https://fonts.googleapis.com/css2?family=Source+Sans+3:wght@400;600;700&display=swap" rel="stylesheet">
<style>
  :root {
    --backdrop: #262626;
    --kraft-light: #d9b88e;
    --kraft-mid: #c49a6a;
    --kraft-dark: #a57c50;
    --ink: #231f1c;
    --band: #2a2623;
    --band-text: #dcbc8f;
  }
  html, body {
    margin: 0;
    padding: 0;
    width: 1200px;
    height: 900px;
    overflow: hidden;
    background: var(--backdrop);
    font-family: "Source Sans 3", sans-serif;
    color: var(--ink);
  }
  .canvas { position: relative; width: 1200px; height: 900px; }
  .card {
    position: absolute;
    top: 306px;
    height: 271px;
    background: radial-gradient(ellipse at 30% 0%, var(--kraft-light) 0%, var(--kraft-mid) 55%, var(--kraft-dark) 100%);
    box-shadow: 2px 3px 6px rgba(0,0,0,0.55);
    overflow: hidden;
  }
  .card-front { left: 149px; width: 439px; }
  .card-back { left: 608px; width: 441px; }

  .brand { position: absolute; left: 0; right: 0; text-align: center; }
  .brand-name {
    font-weight: 700;
    font-size: 54px;
    line-height: 1;
    letter-spacing: 8px;
    margin: 0 0 0 8px;
  }
  .brand-full {
    font-weight: 600;
    font-size: 13.5px;
    line-height: 14px;
    letter-spacing: 0.3px;
    text-transform: uppercase;
    margin-top: 4px;
  }
  .card-front .brand { top: 48px; }
  .card-back .brand { top: 76px; }

  .person {
    position: absolute;
    right: 230px;
    top: 168px;
    text-align: right;
  }
  .person-name { font-weight: 600; font-size: 15.5px; line-height: 18px; text-transform: uppercase; }
  .person-title { font-size: 13px; line-height: 16px; }

  .divider {
    position: absolute;
    left: 227px;
    top: 172px;
    width: 1px;
    height: 40px;
    background: rgba(35,31,28,0.55);
  }
  .contacts {
    position: absolute;
    left: 239px;
    top: 167px;
    list-style: none;
    margin: 0;
    padding: 0;
    font-size: 12.5px;
    line-height: 16px;
  }
  .contacts li { display: flex; align-items: center; gap: 6px; }
  .contacts svg { width: 9px; height: 9px; fill: var(--ink); }

  .address {
    position: absolute;
    left: 0; right: 0;
    top: 230px;
    text-align: center;
    font-size: 12.5px;
  }

  .tagline-band {
    position: absolute;
    left: 0; right: 0;
    top: 197px;
    height: 49px;
    background: var(--band);
    color: var(--band-text);
    display: flex;
    align-items: center;
    justify-content: center;
    font-weight: 700;
    font-size: 13px;
    letter-spacing: 0.2px;
    text-transform: uppercase;
  }
</style>
</head>
<body>
<div class="canvas">

  <section class="card card-front">
    <div class="brand">
      <p class="brand-name">KVOR</p>
      <div class="brand-full">Coherent Lattice of<br>Adaptive Reasoning Method</div>
    </div>

    <div class="person">
      <div class="person-name">Dariel Fenwick</div>
      <div class="person-title">Managing Director</div>
    </div>

    <div class="divider"></div>

    <ul class="contacts">
      <li>
        <svg viewBox="0 0 10 10" aria-hidden="true"><rect x="2.5" y="0" width="5" height="10" rx="1"/><rect x="3.5" y="1.2" width="3" height="6.3" fill="#c49a6a"/></svg>
        888 555 777
      </li>
      <li>
        <svg viewBox="0 0 10 10" aria-hidden="true"><rect x="0" y="2" width="10" height="6.5"/><path d="M0 2 L5 6 L10 2" fill="none" stroke="#c49a6a" stroke-width="1"/></svg>
        info@kvor.com
      </li>
      <li>
        <svg viewBox="0 0 10 10" aria-hidden="true"><circle cx="5" cy="5" r="5"/><path d="M0.5 5 H9.5 M5 0.5 V9.5" stroke="#c49a6a" stroke-width="0.8"/></svg>
        www.kvor.com
      </li>
    </ul>

    <div class="address">Address line one here, Address line two here.</div>
  </section>

  <section class="card card-back">
    <div class="brand">
      <p class="brand-name">KVOR</p>
      <div class="brand-full">Coherent Lattice of<br>Adaptive Reasoning Method</div>
    </div>
    <div class="tagline-band">Amplifying Results for Truly Driven Professionals</div>
  </section>

</div>
</body>
</html>
```